Etiketten-Design für Kräuterbonbon-Metalldose
Katrin Wolber hat sehr viel Talent. Das Design ist absolut kreativ.
Zielgruppe
Unsere Firma FelvoNat verkauft verschiedene Sorten Kräuterbonbons.
Wir brauchen ein Etikett, dass auf eine Metall-Dose (Durchmesser 10 cam, Höhe ca. 3 cm) geklebt wird.
Zielgruppe: jung-alt
Aufgabenstellung
Der Name unserer Kräuterbonbons ist Moospille.
Wir möchten, dass unsere Kunden, wenn sie das Etikett sehen einen Bezug zur Schweiz herstellen können.
Wir verwenden für unsere Bonbons unterschiedliche Kräuter für verschiedene Anwendungen:
Konkret sind erstmal 4 Dosen geplant:
-Kräutermischung aus 16 Kräuter gegen Husten
-Salbei gegen Halsschmerzen
-Anis gegen Magenschmerzen
-Zitrone/Ingwer für die Nerven
Vorderseite: Produktbeschreibung
Rückseite: unsere Herstellerangaben
Größenangaben der Dose: Durchmesser 10 cm, Höhe ca. 3 cm
Im Anhang habe ich Ihnen noch weitere/ genauere Informationen zur Verfügung bereitgestellt!

```html
<!DOCTYPE html>
<html lang="de">
<head>
<meta charset="utf-8">
<title>Moospille – Dosenetiketten</title>
<link rel="stylesheet" href="https://fonts.googleapis.com/css2?family=Questrial&display=swap">
<style>
  :root {
    --bg: #e4e3e4;
    --olive: #6f8a2a;
    --teal: #2a9aa6;
    --red: #e0242b;
    --rim-green: #c9dfb8;
    --rim-yellow: #ece98a;
    --mint-top: #d9f0f2;
    --mint-bottom: #bfe5d8;
    --lemon-top: #f2e93e;
    --lemon-bottom: #f6e43a;
  }
  * { margin: 0; padding: 0; box-sizing: border-box; }
  html, body { width: 766px; height: 1200px; overflow: hidden; background: var(--bg); }
  body { position: relative; font-family: "Questrial", sans-serif; }
  .brand-corner {
    position: absolute; top: 18px; right: 24px;
    font-size: 30px; color: var(--olive); letter-spacing: 0.5px;
  }
  .label { position: absolute; left: 143px; width: 480px; height: 480px; }
  .label--herbs { top: 70px; }
  .label--lemon { top: 660px; }
  .label svg { width: 100%; height: 100%; display: block; }
  .label text { font-family: "Questrial", sans-serif; }
  .label .subline { fill: var(--olive); font-size: 15px; }
  .label .product-name { fill: var(--olive); font-size: 62px; }
  .label .swiss { fill: var(--red); font-size: 14px; }
  .label .content { fill: var(--teal); font-size: 15px; }
  .label .usage { fill: #333; font-size: 8.5px; }
</style>
</head>
<body>
  <div class="brand-corner">Moospille</div>

  <div class="label label--herbs">
    <svg viewBox="0 0 480 480" aria-label="Etikett Kräutermischung">
      <defs>
        <linearGradient id="mint" x1="0" y1="0" x2="0" y2="1">
          <stop offset="0" stop-color="var(--mint-top)"/>
          <stop offset="1" stop-color="var(--mint-bottom)"/>
        </linearGradient>
        <linearGradient id="herbs" x1="0" y1="0" x2="0" y2="1">
          <stop offset="0" stop-color="#4f8a3a"/>
          <stop offset="0.6" stop-color="#7fae5a"/>
          <stop offset="1" stop-color="#7fae5a" stop-opacity="0"/>
        </linearGradient>
        <clipPath id="clipA"><circle cx="240" cy="240" r="222"/></clipPath>
        <path id="arcA1" d="M 58 250 A 182 182 0 0 0 422 250"/>
        <path id="arcA2" d="M 44 250 A 196 196 0 0 0 436 250"/>
      </defs>
      <circle cx="240" cy="240" r="238" fill="var(--rim-green)"/>
      <circle cx="240" cy="240" r="226" fill="none" stroke="#b3cfa1" stroke-width="3"/>
      <g clip-path="url(#clipA)">
        <rect x="0" y="0" width="480" height="480" fill="url(#mint)"/>
        <rect x="0" y="0" width="480" height="150" fill="url(#herbs)" role="img" aria-label="Foto: Kräuterbündel mit Lavendel, Salbei und Thymian"/>
      </g>
      <text class="subline" x="240" y="180" text-anchor="middle">Kräutermischung aus</text>
      <text class="subline" x="240" y="200" text-anchor="middle">16 Kräuter gegen Husten</text>
      <text class="product-name" x="240" y="272" text-anchor="middle">Moospille</text>
      <circle cx="168" cy="300" r="5" fill="var(--red)"/>
      <path d="M168 297.5v5M165.5 300h5" stroke="#fff" stroke-width="1.6"/>
      <text class="swiss" x="178" y="305">Traditional Swiss Formula</text>
      <text class="content" x="240" y="334" text-anchor="middle">INHALT</text>
      <text class="content" x="240" y="353" text-anchor="middle">5,3 OZ</text>
      <text class="content" x="240" y="372" text-anchor="middle">150 g</text>
      <text class="usage"><textPath href="#arcA1" startOffset="50%" text-anchor="middle">Angabe Anwendung MusterText Lorem ipsum dolor sit amet, consetetur sadipscing elitr, sed</textPath></text>
      <text class="usage"><textPath href="#arcA2" startOffset="50%" text-anchor="middle">ipsum dolor sit amet, consetetur sadipscing elitr, sed diam nonumy eirmod tempor invidunt esiut</textPath></text>
    </svg>
  </div>

  <div class="label label--lemon">
    <svg viewBox="0 0 480 480" aria-label="Etikett Zitrone Ingwer">
      <defs>
        <linearGradient id="lemon" x1="0" y1="0" x2="0" y2="1">
          <stop offset="0" stop-color="var(--lemon-top)"/>
          <stop offset="1" stop-color="var(--lemon-bottom)"/>
        </linearGradient>
        <linearGradient id="fruit" x1="0" y1="0" x2="0" y2="1">
          <stop offset="0" stop-color="#d9b23a"/>
          <stop offset="0.6" stop-color="#e8c94a"/>
          <stop offset="1" stop-color="#e8c94a" stop-opacity="0"/>
        </linearGradient>
        <clipPath id="clipB"><circle cx="240" cy="240" r="222"/></clipPath>
        <path id="arcB1" d="M 58 250 A 182 182 0 0 0 422 250"/>
        <path id="arcB2" d="M 44 250 A 196 196 0 0 0 436 250"/>
      </defs>
      <circle cx="240" cy="240" r="238" fill="var(--rim-yellow)"/>
      <circle cx="240" cy="240" r="226" fill="none" stroke="#d8d46a" stroke-width="3"/>
      <g clip-path="url(#clipB)">
        <rect x="0" y="0" width="480" height="480" fill="url(#lemon)"/>
        <rect x="0" y="0" width="480" height="150" fill="url(#fruit)" role="img" aria-label="Foto: Zitronen, Zitronenscheibe und Ingwerwurzeln"/>
      </g>
      <text class="subline" x="240" y="180" text-anchor="middle">Kräutermischung aus</text>
      <text class="subline" x="240" y="200" text-anchor="middle">16 Kräuter gegen Husten</text>
      <text class="product-name" x="240" y="272" text-anchor="middle">Moospille</text>
      <circle cx="168" cy="300" r="5" fill="var(--red)"/>
      <path d="M168 297.5v5M165.5 300h5" stroke="#fff" stroke-width="1.6"/>
      <text class="swiss" x="178" y="305">Traditional Swiss Formula</text>
      <text class="content" x="240" y="334" text-anchor="middle">INHALT</text>
      <text class="content" x="240" y="353" text-anchor="middle">5,3 OZ</text>
      <text class="content" x="240" y="372" text-anchor="middle">150 g</text>
      <text class="usage"><textPath href="#arcB1" startOffset="50%" text-anchor="middle">Angabe Anwendung MusterText Lorem ipsum dolor sit amet, consetetur sadipscing elitr, sed</textPath></text>
      <text class="usage"><textPath href="#arcB2" startOffset="50%" text-anchor="middle">ipsum dolor sit amet, consetetur sadipscing elitr, sed diam nonumy eirmod tempor invidunt esiut</textPath></text>
    </svg>
  </div>
</body>
</html>
```